Public Relations Agency Seeks Wordpress Design and Coding

TRELVOX Studio is a public relations agency specializing in media relations, public affairs and marketing communication.

The site should display the following visual characteristics: professionalism, trustworthiness, high-tech focus, clear and concise design.

The desired colors are royal blue, gray and hints of red.

Design look/feel inspired by this site: http://brightpathgatherings.example/

Specifications:

1. Navigation/Pages/Index:

HOME

ABOUT US

SERVICES

NEWS

CONTACT

---

2. Functionality of/content for each page:

- Home
o Dominant photo (professional, edgy, innovative)
o Simple, straightforward access to/from “Home” from other pages
o Includes logo (attached) and tagline "Unleash the power of communication"
o Direct link to “CONTACT”
o Links to social media accounts: Friendspace, Chirpline, Linkwork

- About Us

o Company profile blurb
o President’s photo with short bio

- Services
o Public Relations
 Strategic communication
 Brand and reputation management
 Community relations
o Media Relations
 News coverage and contacts
 Media training and interview skills
 Crisis communications
o Congressional Affairs
 Public affairs
 Public policy
 Legislative strategy
o Mass Communication
 Speechwriting
 Presentation creation
 Social media
o Marketing Communications
 Business collateral material
 Promotional campaigns
 Special events and tradeshows

- News
o Blog-like page to post information and/or share news from other sites

- Contact
o Standard “Contact Us” form (Name, Email, Phone, Message)
o Direct Contact
 (407) 555-0164
 Marisol@TRELVOXstudio.example

Target Market(s)

Small to large businesses specializing in high technology, defense/military, medicine/healthcare, and wide array of professional services.

Industry/Entity Type

Marketing

Font styles to use
Serif
Sans Serif

Colors
0555a3
ec2027
edf3f7

Requirements
Must have
• -- Project reqires DESIGN - and - fully CODED.

-- Strong SEO

-- Optimized for mobile viewing

Thank you!

```html
<!DOCTYPE html>
<html lang="en">
<head>
<meta charset="utf-8">
<title>TRELVOX Studio – Unleash the Power of Communication</title>
<link href="https://fonts.googleapis.com/css2?family=Arimo:wght@400;700&display=swap" rel="stylesheet">
<style>
:root{
  --red:#b92a1d;
  --red-bright:#d0301f;
  --footer:#c02a1c;
  --grey-text:#555;
  --logo-grey:#666;
  --band:#f3f3f3;
  --white:#fff;
  --field-border:#e2e2e2;
  --placeholder:#b5b5b5;
}
*{margin:0;padding:0;box-sizing:border-box}
html,body{width:1200px;height:2416px;overflow:hidden}
body{font-family:"Arimo",Arial,sans-serif;color:var(--grey-text);background:var(--white);position:relative}
.abs{position:absolute}
.top-rule{left:0;top:0;width:1200px;height:4px;background:var(--red)}
.site-header{left:0;top:4px;width:1200px;height:83px;background:var(--white)}
.brand{left:130px;top:20px;text-align:center;color:var(--logo-grey)}
.brand-name{font-size:36px;font-weight:700;letter-spacing:1px;line-height:38px}
.brand-sub{font-size:13px;letter-spacing:9px;border-top:2px solid var(--logo-grey);margin-top:1px;line-height:16px;padding-left:9px}
.main-nav{top:35px;font-size:15px;color:#444}
.main-nav a{position:absolute;color:inherit;text-decoration:none;white-space:nowrap}
.main-nav a.current{color:var(--red-bright)}
.hero{left:0;top:87px;width:1200px;height:425px;background:radial-gradient(ellipse at 70% 60%,#8a8a8a 0%,#6a6a6a 45%,#5a5a5a 100%)}
.hero-title{left:0;top:130px;width:1200px;text-align:center;color:var(--white);font-weight:700;font-size:48px;line-height:70px;letter-spacing:1px}
.hero-dots{left:572px;top:364px}
.section-title{width:1200px;left:0;text-align:center;color:var(--red);font-size:29px;font-weight:700}
.lead{left:185px;width:830px;text-align:center;font-size:15px;line-height:24px}
.band{left:0;width:1200px;background:var(--band)}
.service-card{top:905px;width:256px;height:310px;background:var(--white);text-align:center}
.service-card h3{font-weight:400;color:var(--red);font-size:19px;margin-top:30px}
.service-card svg{display:block;margin:21px auto 0}
.service-card p{font-size:14px;line-height:25px;margin-top:18px;padding:0 10px;white-space:nowrap}
.news-item{left:130px;width:940px;height:62px}
.news-date{position:absolute;left:0;top:0;width:62px;text-align:center}
.news-month{color:var(--red);font-size:26px;font-weight:700;line-height:28px}
.news-day{color:var(--grey-text);font-size:20px;font-weight:700;margin-top:10px}
.news-rule{position:absolute;left:81px;top:-6px;width:1px;height:60px;background:#999}
.news-body{position:absolute;left:105px;top:-6px;font-size:14px;line-height:24px;width:835px}
.news-body a{color:var(--red);text-decoration:none;font-size:14px}
.btn{background:linear-gradient(#d23424,#b5261a);color:var(--white);text-align:center;font-size:21px;border:none;font-family:inherit}
.field{background:var(--white);border:1px solid var(--field-border);font-size:13px;color:var(--placeholder);padding:20px 18px;width:367px;height:61px}
.site-footer{left:0;top:2040px;width:1200px;height:376px;background:var(--footer);color:var(--white)}
.footer-brand{left:130px;top:48px;color:var(--white)}
.footer-brand .brand-name{font-size:30px;line-height:32px}
.footer-brand .brand-sub{border-color:var(--white);font-size:11px}
.portrait{left:130px;top:112px;width:79px;height:68px;border:2px solid var(--white);background:linear-gradient(135deg,#c9a06a,#8d6a4e)}
.footer-text{font-size:13px;line-height:25px}
.footer-heading{font-size:21px;font-weight:400}
.quick-links a{display:block;color:var(--white);text-decoration:none;font-size:13px;line-height:34px}
.social{left:841px;width:300px;height:48px;font-size:12px}
.social .box{position:absolute;left:0;top:0;width:48px;height:42px;background:var(--white)}
.social .box::after{content:"";position:absolute;left:18px;top:15px;width:12px;height:12px;border-radius:50%;background:var(--footer)}
.social span{position:absolute;left:61px;top:12px}
.footer-rule{left:130px;top:281px;width:939px;height:1px;background:rgba(255,255,255,.7)}
.copyright{left:130px;top:318px;font-size:13px}
</style>
</head>
<body>
<div class="abs top-rule"></div>
<header class="abs site-header">
  <div class="abs brand"><div class="brand-name">TRELVOX</div><div class="brand-sub">STUDIO</div></div>
  <nav class="abs main-nav" style="left:0">
    <a class="current" style="left:503px" href="#">HOME</a>
    <a style="left:607px" href="#about">ABOUT US</a>
    <a style="left:741px" href="#services">SERVICES</a>
    <a style="left:875px" href="#news">NEWS</a>
    <a style="left:979px" href="#contact">CONTACT US</a>
  </nav>
</header>

<section class="abs hero" role="img" aria-label="Grey-toned photo of a world map with a hand reaching toward it">
  <h1 class="abs hero-title">UNLEASH THE POWER OF<br>COMMUNICATION</h1>
  <svg class="abs hero-dots" width="104" height="24" viewBox="0 0 104 24">
    <circle cx="10" cy="12" r="9" fill="none" stroke="#d0301f" stroke-width="2.5"/>
    <circle cx="39" cy="12" r="9" fill="none" stroke="#fff" stroke-width="2.5"/>
    <circle cx="66" cy="12" r="9" fill="none" stroke="#fff" stroke-width="2.5"/>
    <circle cx="92" cy="12" r="9" fill="none" stroke="#fff" stroke-width="2.5"/>
  </svg>
</section>

<section id="about">
  <h2 class="abs section-title" style="top:545px">ABOUT US</h2>
  <p class="abs lead" style="top:601px">Lorem ipsum dolor sit amet, vis ut omnis oratio deterruisset, pro ad tale recteque sadipscing. Ut sale intellegam quo, aliquam rationibus vix ea, an eam mandamus accommodare. Nulla definitionem has ne, unum nulla adolescens usu id, ex sea debitis insolens. An sanctus tincidunt quo, cibo scripta definiebas ne cum.Ne cum graeci legendos, no dolor electram sit. Sea in partiendo explicari. Quod partem ne qui, blandit ponderum signiferumque mei ut.</p>
</section>

<section id="services" class="abs band" style="top:735px;height:533px"></section>
<h2 class="abs section-title" style="top:768px">SERVICES</h2>
<p class="abs lead" style="top:824px">Lorem ipsum dolor sit amet, vis ut omnis oratio deterruisset, pro ad tale recteque sadipscing. Ut sale intellegam quo, aliquam rationibus vix ea, an eam mandamus accommodare. Nulla definitionem has ne, unum nulla adolescens usu id.</p>

<article class="abs service-card" style="left:187px">
  <h3>MEDIA RELATIONS</h3>
  <svg width="112" height="112" viewBox="0 0 112 112">
    <circle cx="56" cy="56" r="54" fill="none" stroke="#b92a1d" stroke-width="3"/>
    <circle cx="56" cy="56" r="48" fill="#b92a1d"/>
    <g fill="#fff"><circle cx="42" cy="40" r="6"/><circle cx="56" cy="38" r="6"/><circle cx="70" cy="40" r="6"/>
    <rect x="36" y="48" width="12" height="20" rx="4"/><rect x="50" y="46" width="12" height="22" rx="4"/><rect x="64" y="48" width="12" height="20" rx="4"/>
    <path d="M30 70 Q56 82 82 70 L82 74 Q56 86 30 74Z"/></g>
  </svg>
  <p>Eum nobis utinam invidunt et.<br>Has sumo oblique principes et,<br>decore minimum vim et.</p>
</article>
<article class="abs service-card" style="left:472px">
  <h3>PUBLIC AFFAIRS</h3>
  <svg width="112" height="112" viewBox="0 0 112 112">
    <circle cx="56" cy="56" r="54" fill="none" stroke="#b92a1d" stroke-width="3"/>
    <circle cx="56" cy="56" r="48" fill="#b92a1d"/>
    <g fill="#fff"><circle cx="50" cy="40" r="6"/><rect x="43" y="48" width="14" height="10" rx="3"/>
    <rect x="40" y="58" width="26" height="6"/><path d="M45 64 H61 L58 80 H48Z"/>
    <rect x="62" y="30" width="14" height="10" rx="3"/></g>
  </svg>
  <p>Eum nobis utinam invidunt et.<br>Has sumo oblique principes et,<br>decore minimum vim et.</p>
</article>
<article class="abs service-card" style="left:757px">
  <h3>COMMUNICATION</h3>
  <svg width="112" height="112" viewBox="0 0 112 112">
    <circle cx="56" cy="56" r="54" fill="none" stroke="#b92a1d" stroke-width="3"/>
    <circle cx="56" cy="56" r="48" fill="#b92a1d"/>
    <g fill="#fff"><rect x="26" y="44" width="16" height="10" transform="rotate(35 34 49)"/>
    <rect x="70" y="44" width="16" height="10" transform="rotate(-35 78 49)"/>
    <path d="M40 56 L56 44 L70 56 L56 70Z"/></g>
  </svg>
  <p>Eum nobis utinam invidunt et.<br>Has sumo oblique principes et,<br>decore minimum vim et.</p>
</article>

<section id="news">
  <h2 class="abs section-title" style="top:1304px">NEWS</h2>
  <article class="abs news-item" style="top:1363px">
    <div class="news-date"><div class="news-month">MAR</div><div class="news-day">22</div></div>
    <div class="news-rule"></div>
    <p class="news-body">Eum nobis utinam invidunt et. Has sumo oblique principes et, decore minimum vim et. Te vel lorem saepe indoctum. Brute periculis constituam est ei. Brute periculis constituam est ei. Brute periculis constituam est ei.<br><a href="#">Read more...</a></p>
  </article>
  <article class="abs news-item" style="top:1455px">
    <div class="news-date"><div class="news-month">MAR</div><div class="news-day">30</div></div>
    <div class="news-rule"></div>
    <p class="news-body">Eum nobis utinam invidunt et. Has sumo oblique principes et, decore minimum vim et. Te vel lorem saepe indoctum. Brute periculis constituam est ei. Brute periculis constituam est ei.<br><a href="#">Read more...</a></p>
  </article>
  <a class="abs btn" href="#" style="left:520px;top:1551px;width:160px;height:53px;line-height:53px;text-decoration:none">VIEW ALL</a>
</section>

<section id="contact" class="abs band" style="top:1651px;height:389px"></section>
<h2 class="abs section-title" style="top:1686px">CONTACT US</h2>
<form>
  <div class="abs field" style="left:216px;top:1759px">Enter Your Name...</div>
  <div class="abs field" style="left:216px;top:1846px">Enter Your Email...</div>
  <div class="abs field" style="left:216px;top:1933px">Enter Your Phone...</div>
  <div class="abs field" style="left:615px;top:1759px;width:369px;height:148px">Enter Your Message</div>
  <div class="abs btn" style="left:615px;top:1935px;width:158px;height:51px;line-height:51px">SUBSCRIBE</div>
</form>

<footer class="abs site-footer">
  <div class="abs brand footer-brand"><div class="brand-name">TRELVOX</div><div class="brand-sub">STUDIO</div></div>
  <div class="abs portrait" role="img" aria-label="Portrait photo of the agency president"></div>
  <p class="abs footer-text" style="left:234px;top:107px;width:300px">Ad oblique civibus evertitur eos, at mutat munere vix, et wisi facilisi scriptorem his. Movet iudico impedit vim id, cu mei nostro ancillae.</p>
  <p class="abs footer-text" style="left:130px;top:192px;width:420px">Homero iracundia consetetur id mea, cum eu diceret ceteros. Vel civibus definitiones ut civibus definitiones ut.</p>
  <h4 class="abs footer-heading" style="left:619px;top:36px">QUICK LINKS</h4>
  <nav class="abs quick-links" style="left:619px;top:71px">
    <a href="#">Home</a><a href="#about">About Us</a><a href="#services">Services</a><a href="#news">News</a><a href="#contact">Contact Us</a>
  </nav>
  <h4 class="abs footer-heading" style="left:841px;top:36px">FOLLOW US</h4>
  <div class="abs social" style="top:82px"><div class="box"></div><span>FRIENDSPACE</span></div>
  <div class="abs social" style="top:138px"><div class="box"></div><span>CHIRPLINE</span></div>
  <div class="abs social" style="top:194px"><div class="box"></div><span>LINKWORK</span></div>
  <div class="abs footer-rule"></div>
  <p class="abs copyright">COPYRIGHT @ 2014 TRELVOXSTUDIO.ALL RIGHTS RESERVED.</p>
</footer>
</body>
</html>
```